Business Card Design

Extremely classy understated design.

Printing in fancy scrip or hand writing.

Conservative color scheme such as black print on beige paper. I am sure you have much better ideas than I would have.

I am involved in a number of different businesses and require a simple elegant business card.

I would like a object on the card, such as, a bald eagle, an antique Halden Crestor, a water fall or a beautiful flower.

My name is: Dwight L. Kessler Not Dwight L. Kessler Investments Investments is my occupation Most of the designs are not acceptable. Very disappointed with results.

Industry/Entity Type

Business

Contact Information for Business Card

Dwight L Kessler
Investments
702 555 0187
mirewoodlk@postvane.net

```html
<!DOCTYPE html>
<html lang="en">
<head>
<meta charset="utf-8">
<title>Dwight L Kessler – Business Card</title>
<link rel="stylesheet" href="https://fonts.googleapis.com/css2?family=Pinyon+Script&family=Open+Sans:wght@400&display=swap">
<style>
  :root {
    --page-bg: #f3f3f1;
    --card-beige: #e8d39f;
    --swirl-beige: #ead8a8;
    --frame-black: #141210;
    --ink-black: #1a1714;
    --ink-grey: #5a5650;
    --eagle-dark: #2a2520;
    --eagle-mid: #4a4035;
  }
  * { margin: 0; padding: 0; box-sizing: border-box; }
  html, body {
    width: 1200px;
    height: 900px;
    overflow: hidden;
    background: var(--page-bg);
  }
  .canvas {
    position: relative;
    width: 1200px;
    height: 900px;
  }
  .business-card {
    position: absolute;
    left: 150px;
    top: 193px;
    width: 900px;
    height: 514px;
    border-radius: 34px;
    background: var(--card-beige);
    overflow: hidden;
  }
  .swirl-pattern {
    position: absolute;
    inset: 0;
    background: radial-gradient(ellipse at 50% 45%, var(--swirl-beige), var(--card-beige) 75%);
  }
  .card-frame {
    position: absolute;
    inset: 16px;
    border: 7px solid var(--frame-black);
    border-radius: 26px;
  }
  .eagle-illustration {
    position: absolute;
    left: 420px;
    top: 50px;
    width: 350px;
    height: 90px;
    background: radial-gradient(ellipse 50% 50% at 50% 50%, var(--eagle-mid) 0%, var(--eagle-dark) 45%, rgba(42, 37, 32, 0) 100%);
    opacity: 0.85;
  }
  .brand-name {
    position: absolute;
    left: 110px;
    top: 170px;
    width: 740px;
    text-align: center;
    font-family: "Pinyon Script", cursive;
    font-size: 86px;
    line-height: 1;
    font-weight: 400;
    color: var(--ink-black);
    white-space: nowrap;
  }
  .occupation {
    position: absolute;
    left: 100px;
    top: 272px;
    width: 760px;
    text-align: center;
    font-family: "Open Sans", sans-serif;
    font-size: 27px;
    letter-spacing: 1.4em;
    padding-left: 1.4em;
    color: var(--ink-grey);
    white-space: nowrap;
  }
  .contact {
    position: absolute;
    left: 250px;
    top: 368px;
    width: 520px;
    text-align: center;
    font-family: "Open Sans", sans-serif;
    color: var(--ink-black);
  }
  .contact-phone {
    font-size: 29px;
    line-height: 1.4;
  }
  .contact-email {
    font-size: 27px;
    letter-spacing: 0.1em;
    line-height: 1.4;
    white-space: nowrap;
  }
</style>
</head>
<body>
  <main class="canvas">
    <section class="business-card">
      <div class="swirl-pattern" role="img" aria-label="Faint light swirl pattern across the beige card"></div>
      <div class="card-frame"></div>
      <div class="eagle-illustration" role="img" aria-label="Illustration of a bald eagle in flight with wings spread"></div>
      <h1 class="brand-name">Dwight L Kessler</h1>
      <p class="occupation">Investments</p>
      <div class="contact">
        <p class="contact-phone">702 555 0187</p>
        <p class="contact-email">mirewoodlk@postvane.net</p>
      </div>
    </section>
  </main>
</body>
</html>
```